Business Card Design

We need a business card designed for our new company. Prefer a black card with white logo & writing.

Contact Information for Business Card

Ted Galloway, address: 7-4812 Fernhollow Road, Abbotsford, BC, V3K 8R2, Office Phone: 604-712-3390, Cell: 604-947-2164, Email: ted@resinworkshub.ca

Colors

Designer to choose only greyscale colors for use in the design.

```html
<!DOCTYPE html>
<html lang="en">
<head>
<meta charset="utf-8">
<title>Resinworks Hub – Business Card</title>
<link href="https://fonts.googleapis.com/css2?family=Poppins:wght@400;700&display=swap" rel="stylesheet">
<style>
  :root {
    --canvas: #a9a9a9;
    --canvas-dark: #8e8e8e;
    --card-black: #231f1e;
    --card-white: #ffffff;
    --ink: #1c1a19;
    --pattern-a: #2a2523;
    --pattern-b: #3a322f;
  }
  * { margin: 0; padding: 0; box-sizing: border-box; }
  html, body { width: 1200px; height: 1015px; overflow: hidden; }
  body {
    font-family: "Poppins", sans-serif;
    background: radial-gradient(ellipse at 50% 40%, var(--canvas) 0%, var(--canvas-dark) 100%);
    position: relative;
  }
  .card {
    position: absolute;
    width: 560px;
    height: 320px;
    box-shadow: 0 14px 30px rgba(0,0,0,0.35);
    overflow: hidden;
  }
  .card--front { left: 110px; top: 150px; display: flex; background: var(--card-white); }
  .card--back { left: 530px; top: 540px; background: var(--card-black); }

  .front__brand-panel {
    width: 250px;
    height: 100%;
    background: var(--card-black);
    display: flex;
    align-items: center;
    justify-content: center;
  }
  .front__divider {
    width: 12px;
    height: 100%;
    border-right: 4px solid var(--card-black);
  }
  .front__contact {
    flex: 1;
    padding: 62px 0 0 34px;
    color: var(--ink);
  }
  .brand-name {
    display: flex;
    align-items: center;
    gap: 10px;
    color: var(--card-white);
    font-weight: 700;
    text-transform: uppercase;
    letter-spacing: 0.02em;
  }
  .brand-name__mark {
    width: 14px; height: 14px;
    border-radius: 50%;
    background: var(--card-white);
    flex: none;
  }
  .brand-name--large { font-size: 26px; }
  .brand-name--small { font-size: 14px; gap: 6px; }
  .brand-name--small .brand-name__mark { width: 9px; height: 9px; }

  .contact__name {
    font-weight: 700;
    font-size: 23px;
    text-transform: uppercase;
    letter-spacing: 0.03em;
    margin-bottom: 10px;
  }
  .contact__list { list-style: none; font-size: 17px; line-height: 1.3; }
  .contact__item { display: flex; align-items: center; gap: 8px; }
  .contact__icon { width: 14px; height: 14px; flex: none; }
  .contact__address { font-size: 17px; line-height: 1.3; margin-top: 20px; font-style: normal; }

  .back__pattern {
    position: absolute; inset: 0;
    background: linear-gradient(135deg, var(--pattern-a) 0%, var(--pattern-b) 50%, var(--pattern-a) 100%);
  }
  .back__brand {
    position: absolute; inset: 0;
    display: flex; align-items: center; justify-content: center;
  }
</style>
</head>
<body>
  <section class="card card--front" aria-label="Business card front">
    <div class="front__brand-panel">
      <div class="brand-name brand-name--large"><span class="brand-name__mark"></span>Resinworks Hub</div>
    </div>
    <div class="front__divider"></div>
    <div class="front__contact">
      <h1 class="contact__name">Ted Galloway</h1>
      <ul class="contact__list">
        <li class="contact__item">
          <svg class="contact__icon" viewBox="0 0 24 24"><path fill="currentColor" d="M6.6 10.8a15 15 0 0 0 6.6 6.6l2.2-2.2a1 1 0 0 1 1-.25 11.4 11.4 0 0 0 3.6.57 1 1 0 0 1 1 1V20a1 1 0 0 1-1 1A17 17 0 0 1 3 4a1 1 0 0 1 1-1h3.5a1 1 0 0 1 1 1c0 1.25.2 2.45.57 3.57a1 1 0 0 1-.25 1z"/></svg>
          604-712-3390
        </li>
        <li class="contact__item">
          <svg class="contact__icon" viewBox="0 0 24 24"><rect x="6" y="2" width="12" height="20" rx="2" fill="none" stroke="currentColor" stroke-width="2"/><circle cx="12" cy="18" r="1.2" fill="currentColor"/></svg>
          604-947-2164
        </li>
        <li class="contact__item">
          <svg class="contact__icon" viewBox="0 0 24 24"><rect x="2" y="5" width="20" height="14" fill="currentColor"/><path d="M2 5l10 8 10-8" fill="none" stroke="#fff" stroke-width="1.6"/></svg>
          ted@resinworkshub.ca
        </li>
      </ul>
      <address class="contact__address">7-4812 Fernhollow Road,<br>Abbotsford, BC, V3K 8R2</address>
    </div>
  </section>

  <section class="card card--back" aria-label="Business card back">
    <div class="back__pattern" role="img" aria-label="Subtle repeating brand pattern on black"></div>
    <div class="back__brand">
      <div class="brand-name brand-name--small"><span class="brand-name__mark"></span>Resinworks Hub</div>
    </div>
  </section>
</body>
</html>
```